OBK Farcoast Logistics Limited

We need the buissnes card to be very exclusive. As we are all young in our company. We need this to be the gate to make our clients feel deep interest for us.

We are focused in as International Trade advisors, and our products go from Oil Tanker Ships to Rubber balls for dogs.

Our Slogan is Trade Made Simple.
And our main marketing will be through Internet.

We were stablished in 2009 In Mexico and we also have offices in Hong Kong.
We have representatives in China and Europe.

Target Market(s)

Is every company or Individual that wants to develop an International Project or product development or Logistic service of Goods and people.
Some of our current projects are Ship Brokerage, Mine Brokerage, Real State and Product Pormotional development.

Industry/Entity Type

It Company

Requirements
Must have
• Our Logo and slogan, and make the card accoriding to the logo.
Nice to have
• Our Colors

```html
<!DOCTYPE html>
<html lang="en">
<head>
<meta charset="utf-8">
<title>OBK – Business Card</title>
<link href="https://fonts.googleapis.com/css2?family=Montserrat:wght@400;500;600;700&display=swap" rel="stylesheet">
<style>
  :root {
    --brand-blue: #1b7cc0;
    --brand-blue-deep: #176fae;
    --brand-green: #8cc63f;
    --ink: #1e1e1e;
    --paper: #ffffff;
    --backdrop: #e8e5e1;
    --accent-circle: #d9ecf8;
  }
  * { box-sizing: border-box; margin: 0; padding: 0; }
  html, body {
    width: 1200px; height: 989px; overflow: hidden;
    background: var(--backdrop);
    font-family: "Montserrat", Arial, sans-serif;
  }
  .canvas { position: relative; width: 1200px; height: 989px; }

  .card { position: absolute; width: 496px; height: 863px; overflow: hidden; }

  /* Front */
  .card-front { left: 82px; top: 54px; background: var(--paper); color: var(--ink); }
  .holder {
    position: absolute; top: 18px; width: 100%; text-align: center;
    font-size: 26px; font-weight: 700; color: var(--brand-blue);
  }
  .holder .position { font-weight: 500; color: var(--brand-green); font-size: 22px; }
  .brand-dot {
    position: absolute; left: 148px; top: 150px;
    width: 200px; height: 200px; border-radius: 50%;
    background: var(--accent-circle);
  }
  .brand-name {
    position: absolute; top: 398px; width: 100%; text-align: center;
    font-size: 90px; font-weight: 600; letter-spacing: 4px; line-height: 1;
    color: var(--brand-green);
  }
  .slogan-front {
    position: absolute; top: 486px; width: 100%; text-align: center;
    font-size: 19px; font-weight: 400; color: var(--brand-blue);
  }
  .contacts {
    position: absolute; top: 584px; width: 100%; text-align: center;
    font-size: 21px; line-height: 38px; color: var(--ink);
  }
  .contacts .line { display: flex; justify-content: center; align-items: center; gap: 8px; }
  .contacts svg { width: 20px; height: 20px; fill: var(--brand-blue); }
  .contacts .spacer { width: 14px; }
  .address { margin-top: 24px; letter-spacing: 0.5px; }
  .wave { position: absolute; left: 0; bottom: 0; width: 496px; height: 130px; }
  .web-front {
    position: absolute; bottom: 20px; width: 100%; text-align: center;
    font-size: 21px; letter-spacing: 2px; color: var(--paper);
  }

  /* Back */
  .card-back { left: 616px; top: 63px; background: var(--brand-blue); color: var(--paper); }
  .back-dot {
    position: absolute; left: 38px; top: 230px;
    width: 420px; height: 420px; border-radius: 50%;
    background: var(--brand-blue-deep);
  }
  .brand-name-back {
    position: absolute; top: 318px; width: 100%; text-align: center;
    font-size: 176px; font-weight: 700; letter-spacing: 8px; line-height: 1;
  }
  .slogan-back {
    position: absolute; top: 494px; width: 100%; text-align: center;
    font-size: 33px; font-weight: 400;
  }
  .web-back {
    position: absolute; bottom: 26px; width: 100%; text-align: center;
    font-size: 23px; letter-spacing: 3.5px; font-weight: 500;
  }
</style>
</head>
<body>
<main class="canvas">

  <section class="card card-front" aria-label="Business card front">
    <p class="holder">Your Name, <span class="position">Position</span></p>
    <div class="brand-dot" aria-hidden="true"></div>
    <h1 class="brand-name">OBK</h1>
    <p class="slogan-front">Trade Made Simple</p>

    <div class="contacts">
      <p class="line">
        <svg viewBox="0 0 24 24" aria-hidden="true"><path d="M6.6 10.8a15.1 15.1 0 0 0 6.6 6.6l2.2-2.2a1 1 0 0 1 1-.25 11.4 11.4 0 0 0 3.6.57 1 1 0 0 1 1 1V20a1 1 0 0 1-1 1A17 17 0 0 1 3 4a1 1 0 0 1 1-1h3.5a1 1 0 0 1 1 1c0 1.25.2 2.45.57 3.57a1 1 0 0 1-.25 1z"/></svg>
        <span>123-456-7890</span>
        <span class="spacer"></span>
        <svg viewBox="0 0 24 24" aria-hidden="true"><path d="M7 2h10a2 2 0 0 1 2 2v16a2 2 0 0 1-2 2H7a2 2 0 0 1-2-2V4a2 2 0 0 1 2-2zm0 3v12h10V5zm5 13.2a1.2 1.2 0 1 0 0 2.4 1.2 1.2 0 0 0 0-2.4z"/></svg>
        <span>123-456-7890</span>
      </p>
      <p class="line">
        <svg viewBox="0 0 24 24" aria-hidden="true"><path d="M3 6h18v12H3zm2 2v.5l7 4.5 7-4.5V8l-7 4.5z"/></svg>
        <span>info@yourcompany.com</span>
      </p>
      <p class="address">00, Complex Name, City, State, 00045</p>
    </div>

    <svg class="wave" viewBox="0 0 496 130" preserveAspectRatio="none" aria-hidden="true">
      <path d="M0 24 C120 50 300 0 496 2 L496 10 C300 10 130 60 0 40 Z" fill="var(--brand-green)"/>
      <path d="M0 34 C130 64 300 14 496 12 L496 130 L0 130 Z" fill="var(--brand-blue)"/>
    </svg>
    <p class="web-front">www.yourcompany.com</p>
  </section>

  <section class="card card-back" aria-label="Business card back">
    <div class="back-dot" aria-hidden="true"></div>
    <h2 class="brand-name-back">OBK</h2>
    <p class="slogan-back">Trade Made Simple</p>
    <p class="web-back">www.yourcompany.com</p>
  </section>

</main>
</body>
</html>
```